Flyer-Design für Fahrzeugpflege&Lackveredelung
Zielgruppe
Die Firma KM Autoglanz - Fahrzeugpflege&Lackveredelung ist ein Kleinunternehmen im Car-Detailing Bereich. Hier steht höchste Qualität und maximale Kundenzufriedenheit auf höchster Stelle.
Zielgruppen sind Fahrzeugbesitzer von hochwertigen Wagen, die höchste Ansprüche auf die Fahrzeugaufbereitung legen.
Aber auch das Tagesgeschäft mit Innenraumaufbereitungen für den Normalverbraucher sind möglich.
Aufgabenstellung
Der Flyer soll modern und hochwertig aussehen.
Größe des Flyers: DIN lang (9,8x21)
2-seitig 4/4 farbig
Farben, Daten und Co bitte auf der Internetseite entnehmen
www.kmautoglanz-beispiel.de

```html
<!DOCTYPE html>
<html lang="de">
<head>
<meta charset="utf-8">
<title>KM Autoglanz – Flyer DIN lang</title>
<link rel="stylesheet" href="https://fonts.googleapis.com/css2?family=Montserrat:wght@300;400;600;700;800;900&display=swap">
<style>
  :root {
    --bg: #2a2a2c;
    --ink-deep: #0b0c12;
    --ink-navy: #141a2e;
    --ink-blue: #1c2545;
    --accent: #2f6fd6;
    --white: #ffffff;
    --paper: #f4f5f7;
    --text-dark: #1b2236;
    --photo-warm-a: #3a2a22;
    --photo-warm-b: #a4532a;
    --photo-cool-a: #2c2f36;
    --photo-cool-b: #8a8e96;
  }
  * { box-sizing: border-box; margin: 0; padding: 0; }
  html, body { width: 1200px; height: 1200px; overflow: hidden; }
  body {
    background: var(--bg);
    font-family: "Montserrat", sans-serif;
    position: relative;
  }
  .flyer {
    position: absolute;
    left: 340px; top: 45px;
    width: 520px; height: 1110px;
    background: linear-gradient(180deg, var(--ink-deep) 0%, var(--ink-navy) 55%, var(--ink-blue) 100%);
    overflow: hidden;
    box-shadow: 0 20px 50px rgba(0,0,0,.45);
  }
  .hero-photo {
    position: absolute;
    left: 0; top: 70px; width: 520px; height: 440px;
    background: linear-gradient(135deg, var(--photo-warm-a) 0%, var(--photo-warm-b) 40%, #2a2422 70%, #1a1616 100%);
    clip-path: polygon(0 12%, 100% 0, 100% 82%, 0 100%);
  }
  .top-band {
    position: absolute; left: 0; top: 0; width: 100%; height: 110px;
    background: var(--ink-deep);
    clip-path: polygon(0 0, 100% 0, 100% 100%, 0 68%);
  }
  .brand {
    position: absolute; right: 34px; top: 120px;
    display: flex; align-items: center; gap: 10px;
    color: var(--white); font-weight: 600; font-size: 24px; letter-spacing: .5px;
  }
  .brand-dot { width: 14px; height: 14px; border: 2px solid var(--white); border-radius: 50%; }
  .headline {
    position: absolute; left: 40px; top: 200px;
    color: var(--white); font-weight: 900; font-size: 50px; line-height: 1.0;
    text-transform: uppercase; letter-spacing: .5px;
    text-shadow: 0 3px 10px rgba(0,0,0,.5);
  }
  .section-title {
    position: absolute; left: 40px; top: 530px;
    color: var(--white); font-weight: 300; font-size: 34px; letter-spacing: 1px;
  }
  .watermark {
    position: absolute; left: 150px; top: 930px;
    color: rgba(0,0,0,.3); font-weight: 400; font-size: 80px; white-space: nowrap;
  }
  .tile {
    position: absolute; width: 230px; height: 100px;
    display: flex; align-items: flex-start; padding: 14px 14px;
    color: var(--white); font-weight: 700; font-size: 16px;
    text-shadow: 0 2px 6px rgba(0,0,0,.7);
  }
  .tile.cool { background: linear-gradient(135deg, var(--photo-cool-a), var(--photo-cool-b) 60%, #4a4d54); }
  .tile.dark { background: linear-gradient(135deg, #1d1f24, #5a5c62 60%, #2a2b30); }
  .tile.seat { background: linear-gradient(135deg, #6f6e6a, #b9b6ae 55%, #7b7872); }
  .tile-ceramic { left: 40px; top: 595px; }
  .tile-interior { left: 40px; top: 705px; }
  .tile-leather { left: 40px; top: 815px; }
  .tile-paint { left: 280px; top: 650px; }
  .tile-upholstery { left: 280px; top: 760px; }
  .tile-glass { left: 280px; top: 870px; }
  .plus-mark {
    position: absolute; left: 36px; top: 984px;
    color: var(--accent); font-weight: 300; font-size: 40px; line-height: 1;
  }
  .extras {
    position: absolute; left: 80px; top: 988px; width: 400px;
    color: var(--white); font-size: 12.5px; line-height: 1.5; font-weight: 400;
  }
  .extras .plus, .extras .more { color: var(--accent); font-weight: 700; }
  .footer {
    position: absolute; left: 0; bottom: 0; width: 100%; height: 58px;
    background: var(--paper);
    display: flex; align-items: center; justify-content: space-between;
    padding: 0 28px;
  }
  .footer-url { font-size: 14px; color: var(--text-dark); }
  .footer-url strong { color: var(--accent); font-weight: 800; }
  .social { display: flex; gap: 10px; }
  .social span { width: 14px; height: 14px; border-radius: 50%; background: var(--text-dark); }
</style>
</head>
<body>
  <main class="flyer">
    <div class="hero-photo" role="img" aria-label="Foto: behandschuhte Hand poliert nassen orangefarbenen Autolack"></div>
    <div class="top-band"></div>
    <div class="brand"><span class="brand-dot"></span>KM Autoglanz</div>
    <h1 class="headline">The only<br>car detailer<br>you need.</h1>

    <h2 class="section-title">Leistungen</h2>
    <div class="watermark" aria-hidden="true">KM Autoglanz</div>

    <div class="tile cool tile-ceramic" role="img" aria-label="Foto: Wasserperlen auf beschichtetem Lack">Keramikbeschichtung</div>
    <div class="tile dark tile-interior" role="img" aria-label="Foto: Cockpit eines Fahrzeugs">Innenraumreinigung</div>
    <div class="tile seat tile-leather" role="img" aria-label="Foto: heller Ledersitz">Lederpflege</div>
    <div class="tile cool tile-paint" role="img" aria-label="Foto: glänzende Lackoberfläche">Lackkorrektur</div>
    <div class="tile seat tile-upholstery" role="img" aria-label="Foto: Stoffsitz im Innenraum">Polsterreinigung</div>
    <div class="tile cool tile-glass" role="img" aria-label="Foto: Hand trägt Versiegelung auf Autoscheibe auf">Scheibenversiegelung</div>

    <div class="plus-mark">+</div>
    <p class="extras">
      <span class="plus">+</span> Lackveredelung <span class="plus">+</span> Lederreparatur
      <span class="plus">+</span> Wachs-Versiegelung <span class="plus">+</span> Bremsenversiegelung
      <span class="plus">+</span> Cabriodach-imprägnierung <span class="plus">+</span> Scheinwerferaufbereitung
      <span class="more">uvm.</span>
    </p>

    <footer class="footer">
      <p class="footer-url"><strong>Mehr unter:</strong> www.kmautoglanz-beispiel.de</p>
      <div class="social" aria-hidden="true"><span></span><span></span><span></span></div>
    </footer>
  </main>
</body>
</html>
```